Harbourline Electrical Solutions

On one side. LOGO (underneath:) Commercial Industrial Residential

- NAME & CONTACT DETAILS

Marcus T. Hollings
Project Manager

(Cell icon) (441) 555-0187
(Email icon) hlelectricalsolutions@mailvento.com
(Facebook & Instagram icons )@hlelectricalsolutions

Other side: LOGO - underneath ELECTRICAL CONSTRUCTION & MAINTENANCE . LED LIGHTING & AUTOMATION . LIFE SAFETY SYSTEMS (FIRE ALARM / SECURITY) . DATA & COMMUNICATION

```html
<!DOCTYPE html>
<html lang="en">
<head>
<meta charset="UTF-8">
<title>Harbourline Electrical Solutions – Business Card</title>
<link href="https://fonts.googleapis.com/css2?family=Montserrat:wght@600;700&family=Open+Sans:ital,wght@0,400;0,600;1,700&display=swap" rel="stylesheet">
<style>
  :root {
    --teal: #1d6e89;
    --teal-dark: #15546a;
    --ink: #1f3a4d;
    --grey: #9aa4ab;
    --paper: #ffffff;
    --backdrop: #e6e8ea;
  }
  * { box-sizing: border-box; margin: 0; padding: 0; }
  html, body {
    width: 800px; height: 1200px; overflow: hidden;
    background: var(--backdrop);
    font-family: "Open Sans", Arial, sans-serif;
  }
  .canvas { position: relative; width: 800px; height: 1200px; }
  .card {
    position: absolute; left: 50px; width: 700px; height: 400px;
    background: var(--paper); overflow: hidden;
    box-shadow: 0 4px 14px rgba(0,0,0,0.12);
  }
  .card--services { top: 150px; }
  .card--contact { top: 650px; }

  .brand { display: flex; align-items: center; gap: 14px; }
  .brand__mark { width: 14px; height: 14px; background: var(--teal); flex: none; }
  .brand__name {
    font-family: "Montserrat", Arial, sans-serif; font-weight: 700;
    color: var(--teal); font-size: 30px; line-height: 1.05; letter-spacing: 0.5px;
    text-transform: uppercase;
  }
  .sectors {
    font-family: "Montserrat", Arial, sans-serif; font-weight: 600;
    color: var(--teal); font-size: 14px; letter-spacing: 2px; margin-top: 10px;
  }

  /* Services side */
  .card--services .brand-block { position: absolute; left: 130px; top: 46px; }
  .services-band {
    position: absolute; left: 0; top: 196px; width: 100%; height: 96px;
    background: var(--teal); color: #fff;
    padding: 20px 0 0 60px; font-size: 16px; line-height: 1.7;
  }
  .social {
    position: absolute; left: 150px; top: 322px;
    display: flex; align-items: center; gap: 10px;
    color: var(--ink); font-size: 15px;
  }
  .social__dot { width: 14px; height: 14px; border-radius: 50%; background: var(--teal); }

  /* Contact side */
  .card--contact .brand-block { position: absolute; left: 60px; top: 36px; }
  .card--contact .brand__name { font-size: 26px; }
  .card--contact .sectors { font-size: 12px; }
  .contact-list {
    position: absolute; left: 60px; top: 160px; list-style: none;
    color: var(--ink); font-size: 14px; line-height: 1.85;
  }
  .contact-list li { display: flex; align-items: center; gap: 10px; }
  .contact-list svg { width: 14px; height: 14px; fill: var(--teal); flex: none; }
  .contact-list .social__dot { width: 12px; height: 12px; margin: 0 1px; }
  .wave { position: absolute; left: 0; bottom: 0; width: 700px; height: 170px; }
  .person {
    position: absolute; right: 50px; bottom: 24px; text-align: right; color: #fff;
  }
  .person__name { font-size: 22px; font-weight: 700; font-style: italic; line-height: 1.3; }
  .person__role { font-size: 14px; margin-top: 2px; }
</style>
</head>
<body>
<div class="canvas">

  <section class="card card--services">
    <div class="brand-block">
      <div class="brand">
        <span class="brand__mark"></span>
        <span class="brand__name">Harbourline<br>Electrical Solutions</span>
      </div>
      <p class="sectors">COMMERCIAL | INDUSTRIAL | RESIDENTIAL</p>
    </div>
    <div class="services-band">
      <p>Electrical Construction &amp; Maintenance &nbsp;|&nbsp; Led Lighting &amp; Automation</p>
      <p>Life Safety Systems (Fire Alarm/Security) &nbsp;|&nbsp; Data &amp; Communication</p>
    </div>
    <div class="social">
      <span class="social__dot"></span>
      <span>@hlelectricalsolutions</span>
    </div>
  </section>

  <section class="card card--contact">
    <div class="brand-block">
      <div class="brand">
        <span class="brand__mark"></span>
        <span class="brand__name">Harbourline<br>Electrical Solutions</span>
      </div>
      <p class="sectors">COMMERCIAL | INDUSTRIAL | RESIDENTIAL</p>
    </div>
    <ul class="contact-list">
      <li>
        <svg viewBox="0 0 24 24" aria-hidden="true"><path d="M6.6 10.8a15.1 15.1 0 0 0 6.6 6.6l2.2-2.2a1 1 0 0 1 1-.25 11.4 11.4 0 0 0 3.6.57 1 1 0 0 1 1 1V20a1 1 0 0 1-1 1A17 17 0 0 1 3 4a1 1 0 0 1 1-1h3.5a1 1 0 0 1 1 1c0 1.25.2 2.45.57 3.57a1 1 0 0 1-.25 1z"/></svg>
        <span>(441) 555-0187</span>
      </li>
      <li>
        <svg viewBox="0 0 24 24" aria-hidden="true"><path d="M3 5h18a1 1 0 0 1 1 1v12a1 1 0 0 1-1 1H3a1 1 0 0 1-1-1V6a1 1 0 0 1 1-1zm9 7.5L20 7H4z"/></svg>
        <span>hlelectricalsolutions@mailvento.com</span>
      </li>
      <li>
        <span class="social__dot"></span>
        <span>@hlelectricalsolutions</span>
      </li>
    </ul>
    <svg class="wave" viewBox="0 0 700 170" preserveAspectRatio="none" aria-hidden="true">
      <path d="M0 74 C 200 14, 360 94, 700 8" fill="none" stroke="var(--grey)" stroke-width="3"/>
      <path d="M0 100 C 200 40, 360 120, 700 30 L700 170 L0 170 Z" fill="var(--teal)"/>
      <path d="M0 145 C 220 105, 380 165, 700 120 L700 170 L0 170 Z" fill="var(--teal-dark)" opacity="0.45"/>
    </svg>
    <div class="person">
      <p class="person__name">Marcus T. Hollings</p>
      <p class="person__role">Project Manager</p>
    </div>
  </section>

</div>
</body>
</html>
```